KorvaNest - Home Income and Business Resources Platform

I am looking for a website template for a multi-purposed website. This website will feature:

1.) Website Directory with Ratings & comments on listings
2.) Company Blog
3.) Homepage with Content (see files for homepage mock)

I would like the Design to have a default width 1170px (wider then normal)

Of course I am looking for Pages for Listings to be designed.

Great looking BLOG Layout: http://journal.plimworks.example/html/blog.html

I would like 4 Versions of a Website Directory Listing "Box"
1.) Basic Listing Box
2.) Sponsored Listing Box
3.) Recommended Listing Box
4.) Stay Away From Listing Box

Information on the Listing Page (Like on a Category Page)
Site Name, Site URL, Website Image, # of Views, Rating and # of Comments

Information on the Listing Details Page:
Same as ABOVE + About website Description, Vornic Score, Category Information

Decent looking examples is here: https://samples.trevolin.example/directory/computers/ and http://www.zqrankhub.example/.

I will include some sketches and screenshots of things I like/looking for. As designers,you have creative freedom and are encouraged to show this. This is Phase one of this project and winning designer is guaranteed to have future work for this project.

Target Market(s)

Directory, business, websites

Industry/Entity Type

Business

Coding

Coded - Design and coding required

Number of Pages Required

5+ page

Font styles to use
Sans Serif

Colors

Designer to choose colors to be used in the design.

Requirements
Must have
• Professional yet clean look. The use of Icons & images
• Unique Look
Should not have
• Any exact copies of any examples I provided

```html
<!DOCTYPE html>
<html lang="en">
<head>
<meta charset="utf-8">
<title>KorvaNest – Home Income and Business Resources</title>
<link href="https://fonts.googleapis.com/css2?family=Roboto:wght@400;500;700&family=Raleway:wght@200;400&family=Lato:wght@400;700&display=swap" rel="stylesheet">
<style>
:root{
  --blue:#0a6ed3;
  --blue-dark:#0659ad;
  --orange:#ff6a0a;
  --text:#333333;
  --muted:#555555;
  --line:#d9d9d9;
  --box-border:#9cc4ec;
  --box-bg:#f8fafc;
  --side-bg:#f7f7f7;
  --white:#ffffff;
}
*{box-sizing:border-box;margin:0;padding:0}
html,body{width:1200px;height:2258px;overflow:hidden;background:var(--white)}
body{position:relative;font-family:"Roboto",Arial,sans-serif;color:var(--text)}
.abs{position:absolute}
h1,h2,h3,h4{font-family:"Lato",Arial,sans-serif;font-weight:400}

/* header */
.brand{left:64px;top:12px}
.brand-name{font-family:"Lato",sans-serif;font-weight:700;font-size:20px;color:var(--blue);line-height:1}
.brand-tag{font-size:9px;color:var(--text);margin-top:2px}
.phone{right:58px;top:19px;font-size:14px;color:var(--text);display:flex;align-items:center;gap:6px}

.nav{left:64px;top:52px;width:1078px;height:33px;background:var(--blue);display:flex;align-items:center;padding:0 16px}
.nav a{color:var(--white);font-size:13px;text-decoration:none;margin-right:15px;font-weight:500}
.nav-social{margin-left:auto;display:flex;gap:11px}
.nav-social span{width:10px;height:10px;background:var(--white);border-radius:2px;display:block}

/* hero */
.hero{left:64px;top:102px;width:1078px;height:361px;background:linear-gradient(120deg,#c9d2d4 0%,#8f9aa0 35%,#d4d9db 60%,#a7b0b5 100%);box-shadow:0 14px 18px -10px rgba(0,0,0,.25)}
.hero-badge{left:111px;top:147px;width:280px;height:280px;border-radius:50%;background:var(--white);border:3px solid var(--blue);box-shadow:0 0 0 6px rgba(255,255,255,.6);text-align:center;padding:55px 30px 0}
.hero-badge h1{font-size:19px;color:var(--blue);line-height:25px}
.hero-badge hr{border:0;border-top:1px solid #999;width:150px;margin:8px auto 10px}
.hero-badge p{font-size:11px;line-height:16px;color:var(--muted)}
.btn{display:inline-block;color:var(--white);font-size:14px;text-align:center;border-radius:2px;font-family:"Roboto",sans-serif}
.btn-orange{background:var(--orange)}
.btn-blue{background:var(--blue)}
.hero-badge .btn{width:143px;height:35px;line-height:35px;margin-top:12px;font-size:15px}

/* features */
.feature{top:528px;height:408px;width:338px;border:1px solid var(--box-border);border-radius:4px;background:var(--box-bg);text-align:center;padding:22px 22px 0}
.feature h2{font-size:18px;color:var(--blue);margin:10px 0 8px}
.feature p{font-size:12.2px;line-height:20.5px;color:var(--text);height:250px;overflow:hidden}
.feature .btn{width:151px;height:37px;line-height:37px;position:absolute;left:93px;bottom:18px}

/* posts */
.post-photo{left:66px;width:244px;height:339px}
.post{left:328px;width:397px}
.post h3{font-size:21px;line-height:25px;text-align:center;color:#222;padding-top:20px}
.post .cat-rule{width:46px;border-top:2px solid #888;margin:9px auto 6px}
.post .cat{font-size:11px;color:var(--blue);text-align:center}
.post p{font-size:12.4px;line-height:23px;margin-top:14px;color:var(--text);width:378px}
.post .by{font-size:12.4px;margin-top:16px}
.post .by span{color:var(--blue);margin:0 6px}
.post .rule{border-top:1px solid var(--line);margin-top:16px}
.post .foot{display:flex;align-items:center;margin-top:8px}
.post .foot .btn{width:151px;height:36px;line-height:36px}
.post .meta{margin-left:auto;display:flex;gap:22px;font-size:11px;margin-right:20px}
.post .meta span{display:flex;align-items:center;gap:6px}

/* sidebar */
.sidebar{left:771px;top:977px;width:367px;height:1230px;background:var(--side-bg)}
.side-title{width:100%;text-align:center;font-size:21px;color:var(--blue);font-family:"Lato",sans-serif}
.side-rule{left:0;width:367px;border-top:1px solid var(--line)}
.avatar{left:116px;top:25px;width:137px;height:137px;border-radius:50%;border:4px solid #d8d8d8;background:radial-gradient(circle at 50% 40%,#d9a88a 0%,#a0663d 55%,#6e4a32 100%)}
.about{left:24px;top:210px;width:330px;font-size:13px;line-height:22px;color:var(--text)}
.social{top:393px;left:0;width:367px;display:flex;justify-content:center;gap:17px}
.social span{width:31px;height:31px;background:var(--blue);position:relative}
.social span::after{content:"";position:absolute;left:9px;bottom:-7px;border:6px solid transparent;border-top-color:var(--blue);border-bottom:0}
.follow{top:436px;width:367px;text-align:center;font-size:10px}
.recent-photo{left:17px;top:550px;width:337px;height:116px;background:linear-gradient(100deg,#8aa24e 0%,#b9a15e 45%,#a8543c 75%,#7e8a3e 100%)}
.recent-title{top:677px;width:367px;text-align:center;font-size:13px;font-weight:700;color:var(--blue)}
.recent-date{left:137px;top:710px;font-size:12.5px}
.recent-date-rule{left:137px;top:704px;width:200px;border-top:1px solid var(--line)}
.arrows{left:165px;top:744px;display:flex;gap:2px}
.arrows span{width:20px;height:20px;background:var(--orange);display:flex;align-items:center;justify-content:center}
.ad-box{left:19px;top:858px;width:329px;height:343px;background:#111;color:var(--white);padding:30px 14px 0}
.ad-box .big{font-family:"Raleway",sans-serif;font-weight:200;font-size:56px;line-height:70px;margin-left:-2px}
.ad-box .small{font-size:12.3px;line-height:19px;margin-top:14px}

/* footer */
.footer-rule{left:0;top:2210px;width:1200px;border-top:1px solid #5b97d6}
.footer{left:64px;top:2222px;width:1078px;display:flex;align-items:center;font-size:11.5px;color:var(--muted)}
.footer .fs{display:flex;gap:6px;margin-right:20px}
.footer .fs span{width:9px;height:9px;background:#777;border-radius:2px}
.footer a{color:var(--muted);text-decoration:none;margin-right:16px}
.footer .copy{margin-left:auto}
</style>
</head>
<body>

<header>
  <div class="abs brand">
    <div class="brand-name">KorvaNest</div>
    <div class="brand-tag">Home Income and Business Resources</div>
  </div>
  <div class="abs phone">
    <svg width="12" height="12" viewBox="0 0 24 24"><path fill="#0a6ed3" d="M6.6 10.8a15 15 0 0 0 6.6 6.6l2.2-2.2c.3-.3.7-.4 1-.2 1.1.4 2.3.6 3.6.6.6 0 1 .4 1 1V20c0 .6-.4 1-1 1A17 17 0 0 1 3 4c0-.6.4-1 1-1h3.5c.6 0 1 .4 1 1 0 1.3.2 2.5.6 3.6.1.3 0 .7-.2 1z"/></svg>
    0800-000-000-000
  </div>
  <nav class="abs nav">
    <a href="#">HOME</a><a href="#">ABOUT</a><a href="#">PAGE TEMPLATES</a><a href="#">SHORTCODES</a><a href="#">SHOP PAGE</a><a href="#">CONTACT</a>
    <div class="nav-social"><span></span><span></span><span></span></div>
  </nav>
</header>

<section>
  <div class="abs hero" role="img" aria-label="Photo of people working at a laptop and reviewing paperwork with a pen"></div>
  <div class="abs hero-badge">
    <h1>Home Income<br>and Business Resources</h1>
    <hr>
    <p>Lorem Ipsum is simply dummy text of the printing and typesettin Lorem Ipsum has been the industry's standard dummy text</p>
    <span class="btn btn-orange">Read More</span>
  </div>
</section>

<section>
  <div class="abs feature" style="left:69px">
    <svg width="38" height="34" viewBox="0 0 38 34"><path d="M10 14 19 6l9 8v9H10z" fill="none" stroke="#222" stroke-width="2"/><rect x="16" y="16" width="6" height="7" fill="#ff6a0a"/><path d="M3 27c5-3 10-3 15 0h12c2 0 2 3 0 3H3z" fill="#ff6a0a" stroke="#222" stroke-width="1.5"/></svg>
    <h2>Home Income Resource Directory</h2>
    <p>Text: Find what you need, when you need it.The KorvaNest website directory is your one-stop pit for anything involved in making money from home, marketing your business or finding a new opportunity. Our modern, community supported ectory will help you keep upto toate with the lastest information in a sensibl Lorem Ipsum simply dummy tethe printing and typesetting industry. Lorem Ipsum has been the industry's standard dummy text ever since the Lorem Ipsum is simply dummy text of the printing and typesettin industry. has been the industry's</p>
    <span class="btn btn-orange">Read More</span>
  </div>
  <div class="abs feature" style="left:438px">
    <svg width="38" height="34" viewBox="0 0 38 34"><rect x="7" y="4" width="24" height="18" fill="none" stroke="#222" stroke-width="2"/><rect x="12" y="13" width="3" height="6" fill="#ff6a0a"/><rect x="17" y="10" width="3" height="9" fill="#0a6ed3"/><rect x="22" y="8" width="3" height="11" fill="#ff6a0a"/><path d="M19 22v10M12 32l7-10 7 10" stroke="#222" stroke-width="2" fill="none"/></svg>
    <h2>Advertising Benefits</h2>
    <p>Text: Everyone needs to advertise and we know just how to get your offer out to the right people. We have many methods including: Text ads, E-mail, Display, newsletter and even some old school methods available to make your next campaign a success. Advertise a website, a link text, full page circular or a small display ad and get results. Every advertiser recieves a dedicated account manager that will handle everything printing and typesetting industry. Lorem Ipsum has been the industry's standard dummy text ever since the</p>
    <span class="btn btn-blue">Read More</span>
  </div>
  <div class="abs feature" style="left:800px">
    <svg width="38" height="34" viewBox="0 0 38 34"><path d="M10 14 19 6l9 8v9H10z" fill="none" stroke="#222" stroke-width="2"/><rect x="16" y="16" width="6" height="7" fill="#ff6a0a"/><path d="M3 27c5-3 10-3 15 0h12c2 0 2 3 0 3H3z" fill="#ff6a0a" stroke="#222" stroke-width="1.5"/></svg>
    <h2>Earning With KorvaNest</h2>
    <p>Text: Join KorvaNest and start earning money. When you share KorvaNest and lock in an advertiser or premium listing, we reward you. Build a downline at any of ourlisted sites when you share KorvaNest with NO extra work. Its all done for you.We also offer a revenue share program for true supporters of our mission. Lorem Ipsum is simply dummy text of the printing and typesetting industry. Lorem Ipsum has been the industry's standard dummy text ever since theLorem Ipsum is simply dummy text of the printing and typesetting industry. Lorem Ipsum has been the</p>
    <span class="btn btn-orange">Read More</span>
  </div>
</section>

<main>
  <div class="abs post-photo" style="top:974px;background:linear-gradient(160deg,#5f7a46 0%,#b98a7a 45%,#e6c9c0 70%,#8a6b55 100%)" role="img" aria-label="Photo of a smiling woman on the phone at a desk"></div>
  <article class="abs post" style="top:974px">
    <h3>Chronic Illness and Starting an<br>Exercise Regimen</h3>
    <div class="cat-rule"></div>
    <div class="cat">Daily Living, Health</div>
    <p>Your general health is intimately connected with the foods and drinks you put into your body. Each person is unique in what food or drink can trigger feeling unhealthy and rundown. It is very easy to lose track of which foods and drinks can be wreaking havoc with your health. A great way to do some detective work</p>
    <div class="by">Written by <span>Mara Velden</span>in<span>August 22, 2016</span></div>
    <div class="rule"></div>
    <div class="foot"><span class="btn btn-orange">Read More</span>
      <div class="meta">
        <span><svg width="12" height="11" viewBox="0 0 12 11"><path d="M6 0C2.7 0 0 2 0 4.5c0 1.4.8 2.6 2 3.4L1.5 11 4.6 9c.5.1.9.1 1.4.1 3.3 0 6-2 6-4.6S9.3 0 6 0z" fill="#0a6ed3"/></svg>05</span>
        <span><svg width="12" height="11" viewBox="0 0 12 11"><path d="M6 11 1 6C-1 4 0 0 3 0c1.3 0 2.3.8 3 1.8C6.7.8 7.7 0 9 0c3 0 4 4 2 6z" fill="#0a6ed3"/></svg>02</span>
      </div>
    </div>
  </article>

  <div class="abs post-photo" style="top:1364px;background:linear-gradient(200deg,#3e4f5a 0%,#8fa0ab 40%,#c9ccc8 65%,#6b5c4e 100%)" role="img" aria-label="Photo of a laptop and car key on a table"></div>
  <article class="abs post" style="top:1364px">
    <h3>Chronic Illness and Starting an<br>Exercise Regimen</h3>
    <div class="cat-rule"></div>
    <div class="cat">Daily Living, Health</div>
    <p>Your general health is intimately connected with the foods and drinks you put into your body. Each person is unique in what food or drink can trigger feeling unhealthy and rundown. It is very easy to lose track of which foods and drinks can be wreaking havoc with your health. A great way to do some detective work</p>
    <div class="by">Written by <span>Mara Velden</span>in<span>August 22, 2016</span></div>
    <div class="rule"></div>
    <div class="foot"><span class="btn btn-blue">Read More</span>
      <div class="meta">
        <span><svg width="12" height="11" viewBox="0 0 12 11"><path d="M6 0C2.7 0 0 2 0 4.5c0 1.4.8 2.6 2 3.4L1.5 11 4.6 9c.5.1.9.1 1.4.1 3.3 0 6-2 6-4.6S9.3 0 6 0z" fill="#0a6ed3"/></svg>05</span>
        <span><svg width="12" height="11" viewBox="0 0 12 11"><path d="M6 11 1 6C-1 4 0 0 3 0c1.3 0 2.3.8 3 1.8C6.7.8 7.7 0 9 0c3 0 4 4 2 6z" fill="#0a6ed3"/></svg>02</span>
      </div>
    </div>
  </article>

  <div class="abs post-photo" style="top:1745px;background:linear-gradient(150deg,#6a4a30 0%,#b07a4a 35%,#d9d6d2 60%,#8aa0b8 100%)" role="img" aria-label="Photo of hands typing on a laptop beside a coffee cup"></div>
  <article class="abs post" style="top:1745px">
    <h3>Chronic Illness and Starting an<br>Exercise Regimen</h3>
    <div class="cat-rule"></div>
    <div class="cat">Daily Living, Health</div>
    <p>Your general health is intimately connected with the foods and drinks you put into your body. Each person is unique in what food or drink can trigger feeling unhealthy and rundown. It is very easy to lose track of which foods and drinks can be wreaking havoc with your health. A great way to do some detective work</p>
    <div class="by">Written by <span>Mara Velden</span>in<span>August 22, 2016</span></div>
    <div class="rule"></div>
    <div class="foot"><span class="btn btn-orange">Read More</span>
      <div class="meta">
        <span><svg width="12" height="11" viewBox="0 0 12 11"><path d="M6 0C2.7 0 0 2 0 4.5c0 1.4.8 2.6 2 3.4L1.5 11 4.6 9c.5.1.9.1 1.4.1 3.3 0 6-2 6-4.6S9.3 0 6 0z" fill="#0a6ed3"/></svg>05</span>
        <span><svg width="12" height="11" viewBox="0 0 12 11"><path d="M6 11 1 6C-1 4 0 0 3 0c1.3 0 2.3.8 3 1.8C6.7.8 7.7 0 9 0c3 0 4 4 2 6z" fill="#0a6ed3"/></svg>02</span>
      </div>
    </div>
  </article>
</main>

<aside class="abs sidebar">
  <div class="abs avatar" role="img" aria-label="Portrait photo of the site author"></div>
  <h4 class="abs side-title" style="top:172px">About Us</h4>
  <p class="abs about">Lorem Ipsum is simply dummy text of the printing and typesetting industry. Lorem Ipsum has been the industry's standard dummy text ever since the 1500s, when an wn printer to</p>
  <h4 class="abs side-title" style="top:318px">Social Media</h4>
  <div class="abs side-rule" style="top:355px"></div>
  <div class="abs social"><span></span><span></span><span></span><span></span><span></span></div>
  <div class="abs follow">Follow Us</div>
  <h4 class="abs side-title" style="top:486px">Recent Posts</h4>
  <div class="abs side-rule" style="top:523px"></div>
  <div class="abs recent-photo" role="img" aria-label="Photo of a woman in a hat blowing bubbles outdoors"></div>
  <div class="abs recent-title">Regular Exercise is a Natural Anti-Inflammatory</div>
  <div class="abs recent-date-rule"></div>
  <div class="abs recent-date">August 22, 2016</div>
  <div class="abs arrows">
    <span><svg width="8" height="10" viewBox="0 0 8 10"><path d="M6 1 2 5l4 4" stroke="#fff" stroke-width="2" fill="none"/></svg></span>
    <span><svg width="8" height="10" viewBox="0 0 8 10"><path d="M2 1l4 4-4 4" stroke="#fff" stroke-width="2" fill="none"/></svg></span>
  </div>
  <h4 class="abs side-title" style="top:800px">Hey Warriors, We Support You!</h4>
  <div class="abs side-rule" style="top:836px"></div>
  <div class="abs ad-box">
    <div class="big">Advertising<br>Benefits</div>
    <div class="small">Action plan chronic chronic illness chronic illness pain chronic pain coping with a chronic illness depression employment energy failure fibro fibromy-algia focus food diary functional medicine goal action plan goals inflammation invisible illness job job hunting life goals live with chronic illness living with long term condition l</div>
  </div>
</aside>

<footer>
  <div class="abs footer-rule"></div>
  <div class="abs footer">
    <div class="fs"><span></span><span></span><span></span></div>
    <a href="#">About Us</a><a href="#">Privacy Policy</a><a href="#">Terms of Use</a><a href="#">Advertise Us</a><a href="#">Help</a>
    <span class="copy">© 2017 Copyright</span>
  </div>
</footer>

</body>
</html>
```